Wordpress Web Design & Coding for velcorahealth.ca

We need a website for a new investment company that is visually grabbing and vibrant. We would like to see a web page that displays trust, growth and confidence. Needs to be responsive and mobile friendly for all browsers and coded for both Android & IOS.

Open to the number of pages and menu items. I selected 4 but if you feel the layout would work better with less I am open to this. Need to sell the people (management team/related businesses) and then show where the invested money will be going (upcoming projects).

Company Info:

Vel Cora is an investment company put together by a group of seasoned business professionals who have come together to combine decades of success in the real estate development, management, financing and medical services. The company will be a full service company offering turn key solutions for medical professionals.

Vel-Cora will focus on providing a full range of services via a group of distinct companies to deliver newly emerging needs of the medical community. The end goal will be to create complete solutions for individuals in the medical community. Our group has experience and success with the conceptualization, construction and financing of medical and dental clinic spaces. Vel-Cora Solutions will be established to accommodate all areas of the development and creation of clinics for medical professionals from building construction to equipment financing and administrations.

You can mention these companies and take photos from their websites. You can also use stock photos.

Our construction partner:
https://318bld.com/projects/

Our equipment leasing partner:
https://www.norvixa.com/

Our Management Team and medical partners

Gil Parish
https://www.ourfirmstance.ca/

Dietmar Vellasquin
https://www.gshdentalservices.com/about-us

PROPOSED PROJECTS (see attachment for details)
Pinegrove Business Park
Holtmere Business Park
Mt. Corwin Ridge Professional

Target Market(s)

Investors

Industry/Entity Type

Investment

Coding

Coded - Design and coding required

Number of Pages Required

4 page

Font styles to use
Sans Serif

Requirements
Must have
• Wordpress – must be both desktop and mobile friendly with fast page load speed
Ability to edit after ourselves in Wordpress
Attractive home page with logo etc.
Logo colours are: for the blue the pantone color is #0355a3
and for the green is #8cc63f

Sections, about us, what we do/services we provide, contact us

```html
<!DOCTYPE html>
<html lang="en">
<head>
<meta charset="utf-8">
<title>Vel-Cora Solutions</title>
<link href="https://fonts.googleapis.com/css2?family=Montserrat:wght@500;600;700;800&family=Arimo:wght@400;700&display=swap" rel="stylesheet">
<style>
:root{
  --blue:#15419a;
  --blue-deep:#0f3483;
  --green:#7bbf33;
  --green-soft:#8cc63f;
  --ink:#333a44;
  --muted:#4a4f57;
  --grey-bg:#f3f3f3;
  --partner-bg:#c3d3ea;
  --footer-grey:#8a8a8a;
  --white:#ffffff;
}
*{box-sizing:border-box;margin:0;padding:0}
html,body{width:1200px;height:3911px;overflow:hidden;background:var(--white)}
body{position:relative;font-family:'Arimo',Arial,sans-serif;color:var(--ink)}
.abs{position:absolute}
.heading{font-family:'Montserrat',Arial,sans-serif;font-weight:800;color:var(--blue);font-size:44px;letter-spacing:.3px}
.heading-center{left:0;width:1200px;text-align:center}
.rule{position:absolute;height:4px;width:64px;background:var(--green)}
.lead{font-size:13.5px;line-height:23px;color:var(--muted);text-align:center;left:300px;width:600px}

/* header */
.site-header{left:0;top:0;width:1200px;height:123px;background:var(--white);border-bottom:1px solid #e6e6e6}
.brand{left:173px;top:52px;font-family:'Montserrat',sans-serif;font-weight:700;font-size:26px;color:var(--blue)}
.phone{left:780px;top:26px;font-family:'Montserrat',sans-serif;font-weight:700;font-size:22px;color:var(--blue);display:flex;align-items:center;gap:8px}
.phone .label{color:var(--green)}
.nav{left:412px;top:80px;display:flex;gap:38px;font-family:'Montserrat',sans-serif;font-weight:700;font-size:15px;color:var(--ink)}
.nav .active{color:var(--green)}

/* hero */
.hero{left:0;top:123px;width:1200px;height:626px;overflow:hidden}
.hero-photo{position:absolute;inset:0;background:radial-gradient(circle at 18% 20%,#e7f2c0 0%,#9cc45a 25%,#456f2a 60%,#2a461c 100%)}
.hero-band{position:absolute;inset:0}
.hero-title{left:174px;top:104px;font-family:'Montserrat',sans-serif;font-weight:800;font-size:57px;line-height:66px;color:var(--white)}

/* about */
.about{left:0;top:749px;width:1200px;height:581px;background:var(--grey-bg)}
.about-text{left:172px;top:157px;width:400px;font-size:13.5px;line-height:23.3px;color:var(--muted)}
.btn{display:flex;align-items:center;background:var(--blue-deep);color:var(--white);font-family:'Montserrat',sans-serif;font-weight:700;font-size:14px;padding-left:15px}
.about-art{left:650px;top:60px;width:400px;height:430px;border-radius:50%;background:radial-gradient(circle,#cfe3a7 0%,#a9c7ec 45%,rgba(243,243,243,0) 72%)}

/* services */
.service-box{width:93px;height:93px;background:var(--green);display:flex;align-items:center;justify-content:center}
.service-title{font-family:'Montserrat',sans-serif;font-weight:700;font-size:16px;color:var(--ink)}
.service-copy{font-size:12.5px;line-height:18px;color:var(--muted);width:230px}
.right{text-align:right}
.center-mark{left:490px;top:1655px;width:220px;text-align:center;font-family:'Montserrat',sans-serif;font-weight:800;font-size:30px;color:var(--blue)}

/* contact */
.contact{left:0;top:1973px;width:1200px;height:532px;background:linear-gradient(90deg,#1b4b98 0%,#2f6a8c 40%,#58a13e 70%,#6db335 100%)}
.contact .heading{color:var(--white)}
.contact .lead{color:#eef3ff}
.form-panel{left:273px;top:209px;width:653px;height:323px;background:var(--green)}
.field{position:absolute;border:1px solid #e7f3d6;color:#f4fbe9;font-size:13px;padding:10px 8px;height:38px}

/* projects */
.projects{left:0;top:2505px;width:1200px;height:730px;background:linear-gradient(180deg,#ffffff 0%,#f4f4f4 55%,#e9e9e9 100%)}
.card{width:260px;height:362px;background:var(--white);box-shadow:0 2px 10px rgba(0,0,0,.08)}
.card-photo{position:absolute;left:20px;top:22px;width:220px;height:250px}
.card-title{position:absolute;left:0;top:285px;width:260px;text-align:center;font-family:'Montserrat',sans-serif;font-weight:700;font-size:16px;line-height:21px;color:var(--ink)}

/* partners */
.partners{left:0;top:3235px;width:1200px;height:320px;background:var(--partner-bg)}
.partner{width:270px;height:172px;background:var(--white);text-align:center}
.partner-label{margin-top:22px;font-family:'Montserrat',sans-serif;font-weight:700;font-size:15.5px;line-height:20px;color:var(--ink)}
.partner-name{margin-top:12px;font-family:'Montserrat',sans-serif;font-weight:700;font-size:19px;color:var(--blue)}

/* footer */
.footer{left:0;top:3555px;width:1200px;height:356px;background:var(--white)}
.footer-brand{left:185px;top:120px;font-family:'Montserrat',sans-serif;font-weight:700;font-size:46px;color:var(--footer-grey)}
.footer-col h4{font-family:'Montserrat',sans-serif;font-weight:700;font-size:16.5px;color:var(--ink);margin-bottom:14px}
.footer-col li{list-style:none;font-size:11.5px;line-height:22px;color:var(--ink)}
.footer-rule{left:172px;top:285px;width:855px;height:1px;background:#d4d4d4}
.social{left:174px;top:323px;display:flex;gap:20px}
.social span{width:20px;height:20px;border:2px solid #3a3a3a;border-radius:50%}
.copyright{left:640px;top:325px;width:387px;text-align:right;font-size:11.5px;color:var(--ink)}
</style>
</head>
<body>

<header class="abs site-header">
  <div class="abs brand">VEL-CORA</div>
  <div class="abs phone">
    <svg width="22" height="22" viewBox="0 0 22 22"><circle cx="11" cy="11" r="11" fill="#7bbf33"/><path d="M7 6.5c.6-.6 1.3-.4 1.6.2l.9 1.7c.2.5.1.9-.3 1.3l-.6.5c.6 1.3 1.7 2.4 3 3l.5-.6c.4-.4.8-.5 1.3-.3l1.7.9c.6.3.8 1 .2 1.6l-.8.8c-.7.7-2 .7-3.5-.2-1.9-1.1-3.4-2.6-4.5-4.5-.9-1.5-.9-2.8-.2-3.5z" fill="#fff"/></svg>
    <span class="label">Call:</span> (604)-555-0187
  </div>
  <nav class="abs nav">
    <span class="active">HOME</span><span>ABOUT</span><span>SERVICES</span><span>PROJECTS</span><span>BLOG</span><span>CONTACT US</span>
  </nav>
</header>

<section class="abs hero">
  <div class="hero-photo" role="img" aria-label="Young plants growing from stacks of coins in warm sunlight"></div>
  <svg class="hero-band" width="1200" height="626" viewBox="0 0 1200 626">
    <polygon points="0,460 0,626 120,626" fill="#6aae2c" opacity=".85"/>
    <polygon points="600,626 1200,380 1200,626" fill="#1d4a9e" opacity=".85"/>
    <polyline points="66,290 36,317 66,344" fill="none" stroke="#fff" stroke-width="3"/>
    <polyline points="1124,290 1154,317 1124,344" fill="none" stroke="#fff" stroke-width="3"/>
  </svg>
  <h1 class="abs hero-title">VELCORA<br>SOLUTIONS</h1>
</section>

<section class="abs about">
  <h2 class="abs heading" style="left:172px;top:63px">About Us</h2>
  <div class="rule" style="left:172px;top:122px;width:106px"></div>
  <p class="abs about-text">Vel-Cora will focus on providing a full range of services via a group of distinct companies to deliver newly emerging needs of the medical community. The end goal will be to create complete solutions for individuals in the medical community. Our group has experience and success with the conceptualization, construction and financing of medical and dental clinic spaces. Vel-Cora Solutions will be established to accommodate all areas of the development and creation of clinics for medical professionals from building construction to equipment financing and administrations.</p>
  <div class="abs btn" style="left:172px;top:406px;width:160px;height:44px">READ MORE
    <svg width="50" height="40" viewBox="0 0 50 40" style="margin-left:6px"><polyline points="6,22 18,34 46,4" fill="none" stroke="#7bbf33" stroke-width="6"/></svg>
  </div>
  <div class="abs about-art" role="img" aria-label="Isometric illustration of a growth chart with bars, rising arrow and coin stacks"></div>
</section>

<section>
  <h2 class="abs heading heading-center" style="top:1408px">Services We Provide</h2>
  <div class="rule" style="left:546px;top:1467px;width:108px"></div>
  <p class="abs lead" style="top:1490px">At vero eos et accusamus et iusto odio dignissimos ducimus qui blanditiis praesentium voluptatum deleni atque corrupti quos dolores et quas molestias except uri sint occaecati cupiditate non provident, similique sunt in culpa qui officia deserunt mollitia animi</p>

  <div class="abs service-box" style="left:173px;top:1620px">
    <svg width="52" height="52" viewBox="0 0 52 52" fill="none" stroke="#fff" stroke-width="2.5"><polyline points="4,26 26,6 48,26"/><polyline points="10,21 10,46 42,46 42,21"/><rect x="20" y="30" width="12" height="16"/></svg>
  </div>
  <div class="abs service-title" style="left:286px;top:1626px">Real Estate Development</div>
  <p class="abs service-copy" style="left:284px;top:1650px">At vero eos et accusamus et iusto odio dignissimos ducimus qui blanditiis pra esentium voluptatum deleni.</p>

  <div class="abs service-box" style="left:932px;top:1620px">
    <svg width="56" height="52" viewBox="0 0 56 52" fill="none" stroke="#fff" stroke-width="2.5"><rect x="22" y="4" width="28" height="36" rx="2"/><circle cx="36" cy="20" r="6"/><path d="M4 30h10l8 6h12M4 46h30l14-10"/></svg>
  </div>
  <div class="abs service-title right" style="left:620px;top:1626px;width:300px">Financing</div>
  <p class="abs service-copy right" style="left:690px;top:1650px">At vero eos et accusamus et iusto odio dignissimos ducimus qui blanditiis pra esentium voluptatum deleni.</p>

  <div class="center-mark abs" style="top:1710px">VEL-CORA</div>

  <div class="abs service-box" style="left:173px;top:1790px">
    <svg width="52" height="56" viewBox="0 0 52 56" fill="none" stroke="#fff" stroke-width="2.5"><circle cx="26" cy="17" r="11"/><path d="M4 54c0-12 9-20 22-20s22 8 22 20z"/><path d="M26 34v20"/></svg>
  </div>
  <div class="abs service-title" style="left:286px;top:1796px">Management</div>
  <p class="abs service-copy" style="left:284px;top:1820px">At vero eos et accusamus et iusto odio dignissimos ducimus qui blanditiis pra esentium voluptatum deleni.</p>

  <div class="abs service-box" style="left:932px;top:1790px">
    <svg width="52" height="56" viewBox="0 0 52 56" fill="none" stroke="#fff" stroke-width="2.5"><path d="M8 4v14c0 8 14 8 14 0V4"/><path d="M15 26v12c0 8 18 8 18 0v-6"/><circle cx="33" cy="27" r="5"/></svg>
  </div>
  <div class="abs service-title right" style="left:620px;top:1796px;width:300px">Medical Services</div>
  <p class="abs service-copy right" style="left:690px;top:1820px">At vero eos et accusamus et iusto odio dignissimos ducimus qui blanditiis pra esentium voluptatum deleni.</p>
</section>

<section class="abs contact">
  <h2 class="abs heading heading-center" style="top:52px">Contact Us</h2>
  <p class="abs lead" style="top:136px">At vero eos et accusamus et iusto odio dignissimos ducimus qui blanditiis praesentium voluptatum deleni atque corrupti quos dolores et quas molestias except uri sint</p>
  <div class="abs form-panel">
    <div class="field" style="left:43px;top:56px;width:275px">Name</div>
    <div class="field" style="left:43px;top:109px;width:275px">Phone</div>
    <div class="field" style="left:43px;top:159px;width:275px">Email</div>
    <div class="field" style="left:336px;top:56px;width:274px;height:142px">Message</div>
    <div class="abs btn" style="left:250px;top:225px;width:138px;height:43px">SUBMIT
      <svg width="48" height="40" viewBox="0 0 48 40" style="margin-left:8px"><polyline points="6,22 18,34 44,4" fill="none" stroke="#7bbf33" stroke-width="6"/></svg>
    </div>
  </div>
</section>

<section class="abs projects">
  <h2 class="abs heading heading-center" style="top:83px">Projects</h2>
  <p class="abs lead" style="top:166px">At vero eos et accusamus et iusto odio dignissimos ducimus qui blanditiis praesentium voluptatum deleni atque corrupti quos dolores et quas molestias except uri sint</p>
  <div class="abs card" style="left:173px;top:268px">
    <div class="card-photo" role="img" aria-label="Black and white photo of a two-storey business park building" style="background:linear-gradient(180deg,#555 0%,#bbb 45%,#3a3a3a 100%)"></div>
    <div class="card-title">Pinegrove<br>Business Park</div>
  </div>
  <div class="abs card" style="left:470px;top:268px">
    <div class="card-photo" role="img" aria-label="Black and white photo of a modern office lobby interior" style="background:linear-gradient(180deg,#2f2f2f 0%,#9a9a9a 50%,#545454 100%)"></div>
    <div class="card-title">Holtmere<br>Business Park</div>
  </div>
  <div class="abs card" style="left:766px;top:268px">
    <div class="card-photo" role="img" aria-label="Aerial black and white photo of a proposed site location" style="background:linear-gradient(135deg,#6a6a6a 0%,#a5a5a5 50%,#4a4a4a 100%)"></div>
    <div class="card-title">Mt. Corwin Ridge<br>Professional</div>
  </div>
</section>

<section class="abs partners">
  <div class="abs partner" style="left:172px;top:75px">
    <p class="partner-label">Our construction<br>partner:</p>
    <p class="partner-name">318 BUILDERS INC.</p>
  </div>
  <div class="abs partner" style="left:465px;top:75px">
    <p class="partner-label">Our equipment<br>leasing partner:</p>
    <p class="partner-name">NORVIXA</p>
  </div>
  <div class="abs partner" style="left:756px;top:75px">
    <p class="partner-label">Our Management Team<br>and medical partners</p>
    <p class="partner-name" style="margin-top:8px">firmstance</p>
    <p class="partner-name" style="margin-top:4px;font-size:15px">GSH</p>
  </div>
</section>

<footer class="abs footer">
  <div class="abs footer-brand">VEL-CORA</div>
  <div class="abs footer-col" style="left:520px;top:54px">
    <h4>Company</h4>
    <ul><li>Lorem ipsum dolo</li><li>Consectetur adipist.</li><li>Fusce eget leo tincid</li><li>Donec consequat</li><li>Praesent elementum</li><li>Jmauris posueret</li></ul>
  </div>
  <div class="abs footer-col" style="left:713px;top:54px">
    <h4>Information</h4>
    <ul><li>Lorem ipsum dolo</li><li>Consectetur adipit.</li><li>Fusce eget leo tincid</li><li>Donec consequat</li><li>Praesent elementum</li><li>Jmauris posuer</li></ul>
  </div>
  <div class="abs footer-col" style="left:898px;top:54px">
    <h4>Other Links</h4>
    <ul><li>Lorem ipsum dolo</li><li>Consectetuscing elit.</li><li>Fusce eget leo tincid</li><li>Donec consequat</li><li>Praesent elementum</li><li>Jmauris posueret</li></ul>
  </div>
  <div class="abs footer-rule"></div>
  <div class="abs social" aria-label="Social links"><span></span><span></span><span></span><span></span><span></span></div>
  <p class="abs copyright">Copyright 2020 &nbsp;All Rights Reserved. Terms of Use | Privacy Policy</p>
</footer>

</body>
</html>
```